Business Card for a Dental Office

The design should communicate integrity, quality and reliability. We also want the card look elegant, simple, but still stand out, different from the traditional-dental-office business card.

Industry/Entity Type

Business

```html
<!DOCTYPE html>
<html lang="en">
<head>
<meta charset="utf-8">
<title>Harbor Crest Dental – Business Card</title>
<link href="https://fonts.googleapis.com/css2?family=Source+Sans+3:wght@400;600;700&display=swap" rel="stylesheet">
<style>
  :root {
    --backdrop: #3a3330;
    --card: #151515;
    --card-edge: #222222;
    --gold: #d6b52a;
    --ink: #ececec;
    --muted: #bdbdbd;
    --divider: #6a6a6a;
  }
  * { margin: 0; padding: 0; box-sizing: border-box; }
  html, body {
    width: 1200px; height: 814px; overflow: hidden;
    background: var(--backdrop);
    font-family: "Source Sans 3", "Myriad Pro", Arial, sans-serif;
  }
  .stage {
    position: relative; width: 1200px; height: 814px;
    display: flex; align-items: center; justify-content: center; gap: 48px;
  }
  .card {
    position: relative; width: 540px; height: 308px;
    background: var(--card);
    border: 1px solid var(--card-edge);
    box-shadow: 0 14px 30px rgba(0,0,0,0.45);
  }

  /* Back side */
  .card-back .brand-mark {
    position: absolute; left: 0; right: 0; top: 96px;
    display: flex; align-items: center; justify-content: center; gap: 12px;
    color: var(--ink); font-weight: 700; font-size: 30px; letter-spacing: 0.5px;
    text-transform: uppercase;
  }
  .brand-square { width: 26px; height: 26px; background: var(--ink); }
  .card-back .web {
    position: absolute; left: 0; right: 0; top: 196px; text-align: center;
    color: var(--ink); font-size: 15px; letter-spacing: 2.6px;
  }

  /* Front side */
  .card-front .brand {
    position: absolute; left: 34px; top: 132px;
    display: flex; align-items: center; gap: 8px;
    color: var(--ink); font-weight: 700; font-size: 21px;
    text-transform: uppercase; letter-spacing: 0.2px;
  }
  .card-front .brand .brand-square { width: 22px; height: 22px; background: var(--gold); }
  .divider {
    position: absolute; left: 290px; top: 56px; width: 1px; height: 196px;
    background: linear-gradient(to bottom, transparent, var(--divider) 20%, var(--divider) 80%, transparent);
  }
  .contact {
    position: absolute; left: 312px; top: 52px;
    color: var(--ink); font-size: 15px; line-height: 19px;
  }
  .person-name { color: var(--gold); font-weight: 600; font-size: 20px; line-height: 24px; }
  .person-role { margin-bottom: 8px; }
  .address { margin-bottom: 6px; }
  .contact-line { display: flex; align-items: center; gap: 7px; }
  .contact-line svg { width: 12px; height: 12px; flex: none; fill: var(--gold); }
  .web-line { padding-left: 19px; }
</style>
</head>
<body>
<main class="stage">

  <section class="card card-back" aria-label="Business card back">
    <div class="brand-mark"><span class="brand-square"></span>Harbor Crest Dental</div>
    <p class="web">www.harborcrest.com</p>
  </section>

  <section class="card card-front" aria-label="Business card front">
    <div class="brand"><span class="brand-square"></span>Harbor Crest Dental</div>
    <div class="divider"></div>
    <div class="contact">
      <p class="person-name">Daniel Reyes</p>
      <p class="person-role">CEO/Founder</p>
      <p class="address">4210 Willow Bend Road<br>Fairview, Oregon 97024</p>
      <p class="contact-line">
        <svg viewBox="0 0 12 12" aria-hidden="true"><path d="M2.2 0.8l2 2.2-1 1.2c.7 1.6 1.9 2.9 3.6 3.7l1.2-1 2.2 2-1.3 1.9C4.8 10.5 1.4 7 .5 2.1z"/></svg>
        503 555 0142
      </p>
      <p class="contact-line">
        <svg viewBox="0 0 12 12" aria-hidden="true"><path d="M3 0h6a1 1 0 0 1 1 1v10a1 1 0 0 1-1 1H3a1 1 0 0 1-1-1V1a1 1 0 0 1 1-1zm0 1.5v7.5h6V1.5z"/></svg>
        503 555 0187
      </p>
      <p class="contact-line">
        <svg viewBox="0 0 12 12" aria-hidden="true"><path d="M3 0h5v3H3zM1 4h10a1 1 0 0 1 1 1v5H0V5a1 1 0 0 1 1-1zm1 2v1h3V6z"/></svg>
        503 555 0199
      </p>
      <p class="contact-line">
        <svg viewBox="0 0 12 12" aria-hidden="true"><path d="M0 2h12v1L6 7 0 3zm0 2.4l6 4 6-4V10H0z"/></svg>
        hello@harborcrest.com
      </p>
      <p class="contact-line">
        <svg viewBox="0 0 12 12" aria-hidden="true"><circle cx="6" cy="6" r="6"/></svg>
        www.harborcrest.com
      </p>
    </div>
  </section>

</main>
</body>
</html>
```